Business Card Design Project

We need a business card for a new technology services company. We develop software and implement software packages for our business customers and although we will begin with just one or two service offerings, our service offerings will expand over time. Our name comes from the an author, KL Barrow, and his "idea" was that opportunity should be based on ability and achievement, not on social status.

We would like to see a design that is standard in its size and shape, but stands apart in its dramatic color contrasts. The card should not use too many colors - the colors used in the background should highlight the brilliant blues of the logo (see attachment) to dramatic effect. The background should not be white.

If necessary, you can change the color of the words "KL Barrow", but not the word "Idea".

Card size should be U.S. standard 2 inches by 3.5 inches and provide for 1/8 inch bleed area on each side.

We need a design for both sides of the business card, one side communicating the company logo and contact information, the other side being purely graphical, incorporating the logo but no other information.

Contact Information Required:
Kate Brook
KateBrook@klbarrowvista.com
614-387-2259

Target Market(s)

Business executives

Industry/Entity Type

Software

Requirements
Must have
• It must have the full company logo on one side, and at least the graphic element of the logo on the other. Either that or the full logo on both.
Nice to have
• It would be nice to have a design that could work without needing two different textures. For example, it would be nice if the entire card could be shiny, not just parts of the card.

It would also be nice if texture is something we could add later.
Should not have
• The card should not use the color green.

```html
<!DOCTYPE html>
<html lang="en">
<head>
<meta charset="utf-8">
<title>KL Barrow Vista – Business Card</title>
<link rel="stylesheet" href="https://fonts.googleapis.com/css2?family=Cinzel:wght@600&family=Inter:wght@400&display=swap">
<style>
  :root {
    --stage: #e9e7e4;
    --card-dark: #1c1d1f;
    --card-mid: #2e3033;
    --brand-blue: #1b9fdc;
    --band-grey: #a7a9ac;
    --band-grey-deep: #8e9093;
    --rule-black: #0d0d0e;
    --text-white: #ffffff;
    --pattern-blue: #1c5b7c;
  }
  * { box-sizing: border-box; margin: 0; padding: 0; }
  html, body {
    width: 1200px; height: 750px; overflow: hidden;
    background: var(--stage);
  }
  .stage {
    position: relative; width: 1200px; height: 750px;
    display: flex; align-items: center; justify-content: center; gap: 40px;
  }
  .card {
    position: relative; width: 520px; height: 297px; overflow: hidden;
    background: linear-gradient(160deg, var(--card-mid) 0%, var(--card-dark) 70%);
    box-shadow: 0 10px 24px rgba(0,0,0,.25);
  }

  /* front */
  .brand-lockup {
    position: absolute; left: 38px; top: 40px; width: 444px; height: 120px;
  }
  .brand-mark {
    position: absolute; right: 40px; top: 0;
    width: 64px; height: 64px; border-radius: 50%;
    background: var(--brand-blue);
  }
  .brand-name {
    position: absolute; left: 0; bottom: 0;
    font-family: "Inter", Arial, sans-serif; font-weight: 400;
    font-size: 44px; letter-spacing: -2px; line-height: 1;
    color: var(--brand-blue);
  }
  .name-band {
    position: absolute; left: 0; top: 176px; width: 100%; height: 40px;
    background: linear-gradient(var(--band-grey) 0 40%, var(--band-grey-deep) 40% 100%);
  }
  .person-name {
    position: absolute; left: 0; right: 0; top: 12px; text-align: center;
    font-family: "Cinzel", Georgia, serif; font-weight: 600;
    font-size: 19px; letter-spacing: 1px; line-height: 1;
    color: var(--text-white);
  }
  .rule { position: absolute; left: 0; top: 216px; width: 100%; height: 7px; background: var(--rule-black); }
  .contact-band {
    position: absolute; left: 0; top: 223px; width: 100%; height: 74px;
    background: var(--brand-blue);
    display: flex; justify-content: center; align-items: flex-start; gap: 26px;
    padding-top: 14px;
    font-family: "Inter", Arial, sans-serif; font-size: 13px; color: var(--text-white);
  }
  .contact-item { display: flex; align-items: center; gap: 6px; }
  .contact-item svg { width: 11px; height: 11px; fill: var(--text-white); }

  /* back */
  .pattern-field {
    position: absolute; inset: 0;
    background:
      radial-gradient(circle at 30% 40%, rgba(28,91,124,.55), transparent 60%),
      radial-gradient(circle at 75% 70%, rgba(28,91,124,.45), transparent 55%),
      linear-gradient(160deg, var(--card-mid), var(--card-dark));
  }
  .back-name {
    position: absolute; left: 0; right: 0; top: 112px; text-align: center;
    font-family: "Inter", Arial, sans-serif; font-weight: 400;
    font-size: 60px; letter-spacing: -3px; line-height: 1;
    color: var(--brand-blue);
  }
</style>
</head>
<body>
<main class="stage">
  <section class="card card-front">
    <div class="brand-lockup">
      <span class="brand-mark"></span>
      <span class="brand-name">KLBarrowVista</span>
    </div>
    <div class="name-band"><p class="person-name">KATE BROOK</p></div>
    <div class="rule"></div>
    <div class="contact-band">
      <span class="contact-item">
        <svg viewBox="0 0 24 24" aria-hidden="true"><path d="M6.6 10.8a15 15 0 0 0 6.6 6.6l2.2-2.2a1 1 0 0 1 1-.25 11.4 11.4 0 0 0 3.6.57 1 1 0 0 1 1 1V20a1 1 0 0 1-1 1A17 17 0 0 1 3 4a1 1 0 0 1 1-1h3.5a1 1 0 0 1 1 1c0 1.25.2 2.45.57 3.57a1 1 0 0 1-.25 1z"/></svg>
        614-387-2259
      </span>
      <span class="contact-item">
        <svg viewBox="0 0 24 24" aria-hidden="true"><path d="M2 6h20v12H2z M3 7l9 6 9-6" fill="none" stroke="#fff" stroke-width="2"/></svg>
        KateBrook@klbarrowvista.com
      </span>
    </div>
  </section>

  <section class="card card-back">
    <div class="pattern-field" role="img" aria-label="Repeating pattern of the brand symbol in muted blue over a dark background"></div>
    <p class="back-name">KLBarrowVista</p>
  </section>
</main>
</body>
</html>
```